New Business Card Design Project LORVANTI-Italy

we are LORVANTI-Italy
our company in the market for 3 years we are luxury cosmetic company and its about time for a facelift :)
i will like to have elegant luxurious and unique business card
that will give the person that get it a unique, luxurious and elegant impression
I'm VERY OPEN FOR NEW IDEAS , even duo i add a few files of things that i see on line and i like them

i add my logo as well
my website is LORVANTI.COM
(if you would like to see the main style that we have)

Target Market(s)

adult that have money :)

Industry/Entity Type

Business

Contact Information for Business Card

Name - Dario Lorvanti
Position - CEO and CO Founder
address - 4817 E Halvern
telephone - 555-384-1926
email - dario@lorvanti.com
fax - 555-384-1926
website - LORVANTI.COM

Colors
000000
959595
fbee3e
ffffff

Requirements
Must have
• big logo in GOLD color
• elegant look
• impressive
Nice to have
• not must but maybe classy pattern background
• not must but maybe emblem
• maybe clear plastic business card
Should not have
• colors
• images

```html
<!DOCTYPE html>
<html lang="en">
<head>
<meta charset="utf-8">
<title>LORVANTI Italy — Business Card</title>
<link rel="stylesheet" href="https://fonts.googleapis.com/css2?family=Cinzel:wght@400;700&family=Open+Sans:wght@400;600&display=swap">
<style>
  :root {
    --canvas: #d0d0d0;
    --card: #111111;
    --card-edge: #1a1a1a;
    --gold: #d9b23c;
    --gold-line: #8a7328;
    --white: #ffffff;
    --shadow: rgba(0, 0, 0, 0.35);
  }
  * { margin: 0; padding: 0; box-sizing: border-box; }
  html, body { width: 1200px; height: 900px; overflow: hidden; }
  body {
    background: var(--canvas);
    position: relative;
    font-family: "Open Sans", Arial, sans-serif;
  }
  .card {
    position: absolute;
    top: 271px;
    width: 457px;
    height: 281px;
    border-radius: 12px;
    background: linear-gradient(160deg, var(--card-edge), var(--card) 55%, #0c0c0c);
    box-shadow: 0 3px 6px var(--shadow);
    overflow: hidden;
  }
  .card--front { left: 137px; }
  .card--back { left: 626px; }

  .brand-name {
    font-family: "Cinzel", "Times New Roman", serif;
    font-weight: 400;
    color: var(--gold);
    position: absolute;
    text-align: center;
    line-height: 1;
  }
  .card--front .brand-name {
    left: 35px; top: 26px; width: 192px;
    font-size: 36px;
  }
  .card--front .brand-sub {
    left: 35px; top: 74px; width: 192px;
    font-size: 15px;
  }
  .card--back .brand-name {
    left: 0; top: 165px; width: 100%;
    font-size: 42px;
  }
  .card--back .brand-sub {
    left: 0; top: 223px; width: 100%;
    font-size: 17px;
  }
  .brand-mark {
    position: absolute;
    left: 178px; top: 40px;
    width: 100px; height: 100px;
    border-radius: 50%;
    background: var(--gold);
  }

  .person {
    position: absolute;
    left: 35px; top: 135px;
  }
  .person__name {
    font-family: "Cinzel", "Times New Roman", serif;
    font-weight: 700;
    font-size: 18px;
    color: var(--gold);
    letter-spacing: 0.3px;
  }
  .person__role {
    font-size: 12.5px;
    color: var(--white);
    margin-top: 1px;
  }
  .divider {
    position: absolute;
    left: 35px; top: 183px;
    width: 393px; height: 1px;
    background: var(--gold-line);
  }
  .address {
    position: absolute;
    left: 35px; top: 238px;
    font-size: 12.5px;
    color: var(--white);
  }
  .contacts {
    position: absolute;
    right: 30px; top: 193px;
    list-style: none;
  }
  .contacts li {
    display: flex;
    align-items: center;
    justify-content: flex-end;
    gap: 7px;
    height: 22.5px;
    font-size: 12.5px;
    color: var(--white);
  }
  .contacts svg { width: 14px; height: 14px; display: block; }
</style>
</head>
<body>

<section class="card card--front" aria-label="Card front">
  <div class="brand-name">LORVANTI</div>
  <div class="brand-name brand-sub">ITALY</div>

  <div class="person">
    <div class="person__name">DARIO LORVANTI</div>
    <div class="person__role">CEO and CO Founder</div>
  </div>

  <div class="divider"></div>

  <div class="address">4817 E Halvern</div>

  <ul class="contacts">
    <li>555-384-1926
      <svg viewBox="0 0 14 14" aria-label="Telephone">
        <circle cx="7" cy="7" r="7" fill="#fff"/>
        <path d="M3.5 6.2c0-1.3 1.6-2.2 3.5-2.2s3.5.9 3.5 2.2l-1.4.4-.3-1H5.2l-.3 1z M4.5 7.2h5l.6 2.8H3.9z" fill="#111"/>
      </svg>
    </li>
    <li>555-384-1926
      <svg viewBox="0 0 14 14" aria-label="Fax">
        <circle cx="7" cy="7" r="7" fill="#fff"/>
        <rect x="5" y="3.3" width="4" height="2.5" fill="#111"/>
        <rect x="3.6" y="6" width="6.8" height="4.6" rx="0.6" fill="#111"/>
        <rect x="5.2" y="8" width="3.6" height="0.8" fill="#fff"/>
      </svg>
    </li>
    <li>dario@lorvanti.com
      <svg viewBox="0 0 14 14" aria-label="Email">
        <circle cx="7" cy="7" r="7" fill="#fff"/>
        <rect x="3.5" y="4.5" width="7" height="5" fill="#111"/>
        <path d="M3.8 4.8 7 7.3l3.2-2.5" fill="none" stroke="#fff" stroke-width="0.7"/>
      </svg>
    </li>
  </ul>
</section>

<section class="card card--back" aria-label="Card back">
  <div class="brand-mark"></div>
  <div class="brand-name">LORVANTI</div>
  <div class="brand-name brand-sub">ITALY</div>
</section>

</body>
</html>
```